New Business Card Design for Manufacturing

We are an engineering/manufacturing company that offers Advanced machining/assembly/engineering services, as well as innovative products for the heavy duty engine cooling markets.

We are looking to get a new business card designed that is clean and modern looking, but still fits the wide range of technical/skilled work we do.

- We hope to use this design as the base for other design work in new Presentations, web, and print work.

Industry/Entity Type

Engineering

Contact Information for Business Card

Our preferred color of blue is (RGB) 22/71/159 but can vary slightly from that color. Our content will be our Logo and full company name (Vantrell Forge Works, Inc.), company address, name, job title, phone number with extension, cell number, fax number, website, and email address on the cards.
We'd like the full company name next to the logo, but we are open to other interpretations of that layout.
Preferably, we would like the back side to be clean with just our logo, and the front to contain all of the contact information.

Colors
2f74b4
0355a3
85abd2

Requirements
Must have
• - Logo, company name, needed content - We are open to interpretation beyond that.
• - Standard size business card.
• - Horizontal orientation.
• - Enough space for lengthy names / job titles (for example, a job title could read "Directory of Human Resources" or "V.P. of Governmental Affairs"). We need this to look clean, whether the title be short (CEO) or long (as described above).

```html
<!DOCTYPE html>
<html lang="en">
<head>
<meta charset="utf-8">
<title>Vantrell Forge Works – Business Card</title>
<link href="https://fonts.googleapis.com/css2?family=Lato:wght@400;700;900&display=swap" rel="stylesheet">
<style>
  :root {
    --brand-blue: #16479f;
    --ink: #2b2e33;
    --muted: #4a4e55;
    --paper: #f3f3f1;
    --backdrop: #cdd2d2;
    --rule: #3a3d42;
  }
  * { box-sizing: border-box; margin: 0; padding: 0; }
  html, body {
    width: 1200px; height: 897px; overflow: hidden;
    background: var(--backdrop);
    font-family: "Lato", sans-serif;
  }
  .sheet {
    position: relative; width: 1200px; height: 897px;
    display: flex; align-items: center; justify-content: center; gap: 60px;
  }
  .card {
    position: relative;
    width: 525px; height: 300px;
    background: var(--paper);
    box-shadow: 0 10px 24px rgba(40, 50, 55, 0.18);
  }
  .brand {
    display: flex; align-items: center; gap: 10px;
    color: var(--brand-blue);
    font-weight: 900; text-transform: uppercase;
    line-height: 1.0;
  }
  .brand-mark {
    flex: none; background: var(--brand-blue);
  }
  .card-front .brand {
    position: absolute; top: 38px; right: 34px;
    font-size: 15px; letter-spacing: 0.04em;
  }
  .card-front .brand-mark { width: 30px; height: 30px; }
  .contact {
    position: absolute; left: 36px; bottom: 36px;
    color: var(--ink);
  }
  .person-name {
    color: var(--brand-blue);
    font-size: 22px; font-weight: 700; letter-spacing: 0.08em;
    text-transform: uppercase;
  }
  .person-title {
    font-size: 13.5px; color: var(--muted); margin-top: 2px;
  }
  .divider {
    width: 44px; height: 1.5px; background: var(--rule);
    margin: 12px 0 12px;
  }
  .contact-line {
    font-size: 12.5px; letter-spacing: 0.04em; line-height: 1.6;
  }
  .contact-line .web, .company-line { color: var(--brand-blue); }
  .card-back .brand {
    position: absolute; inset: 0; justify-content: center;
    font-size: 24px; letter-spacing: 0.04em;
  }
  .card-back .brand-mark { width: 44px; height: 44px; }
</style>
</head>
<body>
  <main class="sheet">
    <section class="card card-front" aria-label="Business card front">
      <div class="brand">
        <span class="brand-mark"></span>
        <span class="brand-name">Vantrell<br>Forge<br>Works <small style="font-size:8px">Inc</small></span>
      </div>
      <div class="contact">
        <h1 class="person-name">Dorian Haskell</h1>
        <p class="person-title">Directory of Human Resources</p>
        <div class="divider"></div>
        <p class="contact-line">P: 1234- ext | C: 555-318-4620 | F: (555)318-4621</p>
        <p class="contact-line">E: dhaskell@vantrellforge.com | <span class="web">www.vantrellforge.com</span></p>
        <p class="contact-line company-line">Vantrell Forge Works, Inc.</p>
        <p class="contact-line">4870 Harlow Ave. Brightwater, FL 33990</p>
      </div>
    </section>

    <section class="card card-back" aria-label="Business card back">
      <div class="brand">
        <span class="brand-mark"></span>
        <span class="brand-name">Vantrell<br>Forge<br>Works <small style="font-size:11px">Inc</small></span>
      </div>
    </section>
  </main>
</body>
</html>
```